Business Card & Email Signature Design || Upmarket + Luxury

Rima Vale Honey, a New Zealand Manuka Honey company needs a Business Card & Email Signature design.

Our logo's are attached in Gold & Black versions, feel free to be creative with how you use the logo and it's patterns in your design.

Style:
- Looking for an Elegant, Luxurious, Upmarket feel.
- Black/Matte Black Card, Gold Foil, UV Embossing

Information to Add:

- Logo
- Company Name: Rima Vale Honey
- Name: Martin Holloway
- Title: Creative Director
- Phone: +64 2815 96 417
- Email: martin@rimavalehoney.example.nz
- Website: www.rimavalehoney.example.nz

- Socials: ***For email Signature Only***
- Facebook: https://www.facebook.com/rimavalehoney/
- Instagram: https://www.instagram.com/rimavalehoney/

Target Market(s)

Asia/Europe Luxury, Upmarket

Contact Information for Business Card

- Logo
- Name: Martin Holloway
- Phone: +64 2815 96 417

Font styles to use
Other font styles liked:
• Champagne & Limousines (Attached)

Requirements
Must have
• Business Card & Email Signature Design.

Looking for a Sleek, Luxury, Upmarket Design.

```html
<!DOCTYPE html>
<html lang="en">
<head>
<meta charset="utf-8">
<title>Rima Vale Honey — Business Card</title>
<link rel="stylesheet" href="https://fonts.googleapis.com/css2?family=Cinzel:wght@500&family=Josefin+Sans:wght@300;400&family=Poppins:wght@300&display=swap">
<style>
  :root {
    --surface: #a7acad;
    --card: #141414;
    --gold: #d4b35f;
    --lime: #9ccc1c;
    --cyan: #27b4cf;
    --white: #f2f2f2;
  }
  * { margin: 0; padding: 0; box-sizing: border-box; }
  html, body { width: 1200px; height: 824px; overflow: hidden; }
  body { background: var(--surface); position: relative; }

  .card {
    position: absolute;
    width: 540px;
    height: 309px;
    background: var(--card);
    box-shadow: 0 4px 14px rgba(0,0,0,0.35);
  }
  .card--front { left: 50px; top: 300px; }
  .card--back { left: 610px; top: 215px; }

  /* Front */
  .brand {
    position: absolute;
    left: 0; right: 0; top: 70px;
    display: flex; flex-direction: column; align-items: center;
  }
  .brand__dot {
    width: 46px; height: 46px; border-radius: 50%;
    background: var(--gold);
    margin-bottom: 16px;
  }
  .brand__name {
    font-family: "Josefin Sans", sans-serif;
    font-weight: 400;
    font-size: 30px;
    letter-spacing: 5px;
    color: var(--gold);
    text-transform: uppercase;
  }
  .front__web {
    position: absolute;
    left: 0; right: 0; top: 212px;
    text-align: center;
    font-family: "Josefin Sans", sans-serif;
    font-weight: 300;
    font-size: 15px;
    letter-spacing: 2px;
    color: var(--cyan);
  }

  /* Back */
  .holder {
    position: absolute;
    left: 38px; top: 36px;
    display: flex; align-items: center; gap: 12px;
  }
  .holder__dot {
    width: 34px; height: 34px; border-radius: 50%;
    background: var(--gold);
  }
  .holder__name {
    font-family: "Cinzel", serif;
    font-weight: 500;
    font-size: 19px;
    letter-spacing: 1px;
    color: var(--gold);
  }
  .holder__title {
    font-family: "Josefin Sans", sans-serif;
    font-weight: 300;
    font-size: 14px;
    color: var(--lime);
    margin-top: 1px;
  }
  .contact {
    position: absolute;
    left: 38px; bottom: 34px;
    list-style: none;
    font-family: "Poppins", sans-serif;
    font-weight: 300;
    font-size: 13px;
    color: var(--white);
  }
  .contact__item { display: flex; align-items: center; gap: 9px; line-height: 21px; }
  .contact__icon { width: 11px; height: 11px; fill: none; stroke: var(--gold); stroke-width: 1.6; }
</style>
</head>
<body>
  <section class="card card--front">
    <div class="brand">
      <div class="brand__dot"></div>
      <div class="brand__name">Rima Vale Honey</div>
    </div>
    <div class="front__web">www.RimaValeHoney.example.nz</div>
  </section>

  <section class="card card--back">
    <div class="holder">
      <div class="holder__dot"></div>
      <div>
        <div class="holder__name">MARTIN HOLLOWAY</div>
        <div class="holder__title">Creative Director</div>
      </div>
    </div>
    <ul class="contact">
      <li class="contact__item">
        <svg class="contact__icon" viewBox="0 0 12 12"><path d="M2 1.5 L4.5 1.5 L5.2 4 L3.8 5 Q5 7.3 7 8.2 L8 6.8 L10.5 7.5 L10.5 10 Q5.5 10.5 2 6 Q1.2 4 2 1.5 Z"/></svg>
        <span>+64 2815 96 417</span>
      </li>
      <li class="contact__item">
        <svg class="contact__icon" viewBox="0 0 12 12"><rect x="1" y="2.5" width="10" height="7"/><path d="M1 2.5 L6 6.5 L11 2.5"/></svg>
        <span>martin@rimavalehoney.example.nz</span>
      </li>
      <li class="contact__item">
        <svg class="contact__icon" viewBox="0 0 12 12"><circle cx="6" cy="6" r="5"/><ellipse cx="6" cy="6" rx="2.2" ry="5"/><path d="M1 6 H11"/></svg>
        <span>www.rimavalehoney.example.nz</span>
      </li>
    </ul>
  </section>
</body>
</html>
```